Business Cards for new orthopaedic surgery practice

My husband and I are starting our own orthopaedic surgery practice. We are looking for a business card that is uniform, but one will have my name/title and the other will have his. You can just create one design with my name on it for now. But when I choose your design as the winning design I will ask that you add another copy with his name/title.

We are looking for classy, simple, elite all in one. We like dark blues/a little gold/yellow. Something that goes with our logo. We want our logo incorporated. Here is all the info you need:
Business name: RV Bone & Vitality Center
Location: 38517 North Willowmere Ave
Maple Ridge, FL 33499
Phone: 954-218-4063
Fax: 954-582-7341
Email: info@myrvbonecare.example

Names: Lydia Vance, M.D.
Board Certified Hand and Upper Extremity Surgeon

Ebo Dansu, M.D.
Board Certified Hip & Knee Replacement/General Orthopaedic Surgeon

Can decide what you want to put on the back. Maybe a slogan:
Rooted in Care. Focused on You

I am just going to upload our logo. The only thing is if we select you as the winning design, the location, and phone numbers may change. We will need your help to update that once fully solidified.

Industry/Entity Type

Medical

Contact Information for Business Card

Colors
0054AA
0677BA
7BADD7
CADEEF
E8F1F8
0094D4
00A9DD
6FCCEA
C7EBF8
E9F6FB

Requirements
Must have
• class, appeal,
Should not have
• We want to air on the side of masculine if we are looking at masculine vs. feminine feel. But we still want it classy, sophisticated, and something we will love

```html
<!DOCTYPE html>
<html lang="en">
<head>
<meta charset="utf-8">
<title>RV Bone &amp; Vitality Center — Business Card</title>
<link href="https://fonts.googleapis.com/css2?family=Poppins:wght@300;400;500;600&display=swap" rel="stylesheet">
<style>
  :root {
    --page-bg: #1c1d22;
    --card-white: #ffffff;
    --navy: #25388a;
    --navy-deep: #1f2f78;
    --navy-soft: #3a52a8;
    --brand-blue: #24398c;
    --accent-cyan: #19b2e2;
    --text-grey: #8a8a8a;
    --rule-grey: #a9a9a9;
  }
  * { box-sizing: border-box; margin: 0; padding: 0; }
  html, body {
    width: 1200px; height: 900px; overflow: hidden;
    background: var(--page-bg);
    font-family: "Poppins", sans-serif;
  }
  .sheet {
    width: 1200px; height: 900px;
    display: flex; flex-direction: column; align-items: center; justify-content: center;
    gap: 24px;
  }
  .card {
    position: relative;
    width: 680px; height: 390px;
    overflow: hidden;
    box-shadow: 0 12px 30px rgba(0,0,0,.45);
  }

  /* Brand lockup (shared) */
  .brand {
    position: absolute;
    display: flex; align-items: center; gap: 14px;
  }
  .brand-mark { width: 18px; height: 18px; flex: none; }
  .brand-divider { width: 2px; height: 86px; flex: none; }
  .brand-name {
    font-size: 21px; font-weight: 500; line-height: 1.2;
    text-transform: uppercase; letter-spacing: 1px;
  }

  /* Front */
  .card-front { background: var(--card-white); }
  .brand-front { right: 40px; top: 70px; }
  .brand-front .brand-mark,
  .brand-front .brand-divider { background: var(--brand-blue); }
  .brand-front .brand-name { color: var(--brand-blue); }

  .person { position: absolute; left: 40px; top: 148px; }
  .person-name {
    font-size: 24px; font-weight: 600; color: var(--accent-cyan); letter-spacing: .3px;
    line-height: 1.2;
  }
  .person-title {
    font-size: 16px; font-weight: 400; color: var(--text-grey); margin-top: 4px;
  }
  .person-rule {
    position: absolute; left: 40px; top: 212px; width: 600px; height: 1.5px;
    background: var(--rule-grey);
  }
  .contacts {
    position: absolute; left: 40px; top: 226px; list-style: none;
    font-size: 15px; font-weight: 300; color: var(--text-grey); line-height: 26px;
  }
  .contacts li { display: flex; align-items: center; gap: 8px; }
  .contacts svg { width: 13px; height: 13px; fill: var(--accent-cyan); flex: none; }
  .address {
    position: absolute; right: 40px; top: 300px;
    font-size: 15px; font-weight: 300; color: var(--text-grey); line-height: 24px;
  }

  /* Back */
  .card-back { background: var(--navy); }
  .back-pattern {
    position: absolute; inset: 0;
    background: linear-gradient(135deg, var(--navy-deep) 0%, var(--navy) 50%, var(--navy-soft) 100%);
  }
  .brand-back { right: 60px; bottom: 56px; }
  .brand-back .brand-mark,
  .brand-back .brand-divider { background: var(--card-white); }
  .brand-back .brand-name { color: var(--card-white); }
</style>
</head>
<body>
<main class="sheet">
  <section class="card card-front" aria-label="Business card front">
    <div class="brand brand-front">
      <span class="brand-mark"></span>
      <span class="brand-divider"></span>
      <span class="brand-name">RV Bone &amp;<br>Vitality<br>Center</span>
    </div>
    <div class="person">
      <h1 class="person-name">Lydia Vance, M.D.</h1>
      <p class="person-title">Hand and Upper Extremity Surgery</p>
    </div>
    <div class="person-rule"></div>
    <ul class="contacts">
      <li>
        <svg viewBox="0 0 24 24" aria-hidden="true"><path d="M6.6 10.8a15.1 15.1 0 0 0 6.6 6.6l2.2-2.2c.3-.3.7-.4 1-.2 1.1.4 2.3.6 3.6.6.6 0 1 .4 1 1V20c0 .6-.4 1-1 1A17 17 0 0 1 3 4c0-.6.4-1 1-1h3.5c.6 0 1 .4 1 1 0 1.3.2 2.5.6 3.6.1.3 0 .7-.2 1z"/></svg>
        954-218-4063
      </li>
      <li>
        <svg viewBox="0 0 24 24" aria-hidden="true"><path d="M6 3h10v5H6zM4 9h16a2 2 0 0 1 2 2v7h-4v3H6v-3H2v-7a2 2 0 0 1 2-2zm4 7v3h8v-3z"/></svg>
        954-582-7341
      </li>
      <li>
        <svg viewBox="0 0 24 24" aria-hidden="true"><path d="M3 5h18a1 1 0 0 1 1 1v12a1 1 0 0 1-1 1H3a1 1 0 0 1-1-1V6a1 1 0 0 1 1-1zm9 7 8-5H4z"/></svg>
        info@myrvbonecare.example
      </li>
    </ul>
    <p class="address">38517 North Willowmere Ave<br>Maple Ridge, FL 33499</p>
  </section>

  <section class="card card-back" aria-label="Business card back">
    <div class="back-pattern" role="img" aria-label="Repeating tonal pattern of the practice emblem across the navy background"></div>
    <div class="brand brand-back">
      <span class="brand-mark"></span>
      <span class="brand-divider"></span>
      <span class="brand-name">RV Bone &amp;<br>Vitality<br>Center</span>
    </div>
  </section>
</main>
</body>
</html>
```